Custom unique Stationary design for Logistics company

We need a custom, unique , elegant and luxurious full stationary design using our new logo, following these guidelines:
1- Business card: double sided, both sides uses the navy blue as the background main color (same as the code of the navy blue used in our logo).
2- envelope and folder: also use the same navy blue as the main background color.
3- book cover( notepad cover) : same thing with the navy blue
4- letterhead: feel free to use the combination of the colors in our logo.
5- rest of the items are up to your creativity

Target Market(s)

corporates and other businesses

Industry/Entity Type

Logistics and heavy machines contractors

Requirements
Must have
• Letterhead, business card, envelope, notepad cover, paper, file
Nice to have
• navy blue to be main background color for business card, envelope, notepad cover

```html
<!DOCTYPE html>
<html lang="en">
<head>
<meta charset="utf-8">
<title>Kestrel Cargo Company – Stationery Set</title>
<link href="https://fonts.googleapis.com/css2?family=Montserrat:wght@500;700;800&display=swap" rel="stylesheet">
<style>
  :root{
    --navy:#0f557f;
    --navy-deep:#0a3f60;
    --navy-light:#1d6e9c;
    --orange:#f26a3a;
    --paper:#ffffff;
    --ink:#1e3f57;
    --backdrop:#8fb8e2;
    --muted:#c9d8e4;
  }
  *{box-sizing:border-box;margin:0;padding:0}
  html,body{width:1200px;height:904px;overflow:hidden}
  body{background:var(--backdrop);font-family:"Montserrat",sans-serif;position:relative;color:var(--ink)}
  .item{position:absolute;box-shadow:0 6px 14px rgba(10,40,70,.25)}

  .wordmark{font-family:"Montserrat",sans-serif;font-weight:800;letter-spacing:.04em;text-transform:uppercase;line-height:1;display:flex;align-items:center;gap:6px;white-space:nowrap}
  .wordmark .dot{width:9px;height:9px;border-radius:50%;background:var(--orange);flex:none}
  .wordmark.on-light{color:var(--navy)}
  .wordmark.on-dark{color:#fff}
  .wordmark.compact{gap:4px}
  .wordmark.compact .dot{width:6px;height:6px}

  /* Letterhead */
  .letterhead{left:44px;top:32px;width:344px;height:490px;background:var(--paper)}
  .letterhead .head-rule{position:absolute;top:40px;left:0;right:0;height:4px;background:var(--navy)}
  .letterhead .head-rule::before{content:"";position:absolute;left:0;top:0;width:28px;height:4px;background:var(--orange)}
  .letterhead .wordmark{position:absolute;left:36px;top:20px;font-size:14px;background:var(--paper);padding-right:8px}
  .letterhead .footer-info{position:absolute;left:6px;bottom:14px;font-size:5px;font-weight:700;color:var(--ink);white-space:nowrap}
  .letterhead .footer-bar{position:absolute;left:0;right:0;bottom:0;height:10px;background:linear-gradient(90deg,var(--orange) 0 25%,var(--navy) 25% 100%)}
  .letterhead .site{position:absolute;right:0;bottom:4px;width:82px;height:16px;background:var(--navy);color:#fff;font-size:6px;font-weight:700;display:flex;align-items:center;justify-content:center}

  /* Folder */
  .folder{left:440px;top:48px;width:720px;height:430px;background:var(--navy);display:flex;border-top:4px solid var(--orange)}
  .folder .panel{position:relative;width:360px;height:100%;overflow:hidden}
  .folder .panel + .panel{border-left:2px solid var(--navy-deep)}
  .folder svg.wave{position:absolute;inset:0}
  .folder .back .wordmark{position:absolute;left:28px;top:70px;font-size:20px;z-index:2}
  .folder .front .wordmark{position:absolute;left:46px;top:96px;font-size:26px}
  .folder .front .tagline{position:absolute;left:46px;top:132px;font-size:8px;font-weight:700;letter-spacing:.12em;color:var(--muted);text-transform:uppercase}
  .folder .contacts{position:absolute;left:0;right:0;bottom:40px;display:flex;justify-content:space-around;z-index:2}
  .folder .contact{display:flex;flex-direction:column;align-items:center;gap:6px;font-size:6.5px;font-weight:700;color:#fff;text-align:center}
  .folder .contact .badge{width:22px;height:22px;border-radius:50%;background:var(--orange);display:flex;align-items:center;justify-content:center}

  /* Business cards */
  .card{width:210px;height:120px;background:var(--navy);overflow:hidden}
  .card-front{left:56px;top:566px}
  .card-front .wordmark{position:absolute;left:22px;top:40px;font-size:15px}
  .card-front .tagline{position:absolute;left:22px;top:62px;font-size:6px;font-weight:700;letter-spacing:.12em;color:var(--muted)}
  .card-front .site{position:absolute;left:0;right:0;bottom:18px;text-align:center;font-size:7px;font-weight:700;color:#fff}
  .card-back{left:56px;top:742px}
  .card-back .wordmark{position:absolute;left:10px;top:56px;font-size:8px}
  .card-back .divider{position:absolute;left:108px;top:22px;width:1px;height:74px;background:rgba(255,255,255,.5)}
  .card-back .details{position:absolute;left:115px;top:22px;font-size:6px;font-weight:700;color:#fff;display:flex;flex-direction:column;gap:5px;white-space:nowrap}
  .card-back .name{color:var(--orange);font-size:7.5px}
  .card-back .role{font-weight:500;margin-top:-4px}
  .card-back .stripe{position:absolute;left:0;right:0;bottom:10px;height:3px;background:linear-gradient(90deg,var(--orange) 0 40%,#fff 40% 60%,var(--orange) 60%)}
  .line-icon{display:inline-flex;align-items:center;gap:4px}

  /* Envelope */
  .envelope{left:336px;top:560px;width:436px;height:290px;background:var(--paper);overflow:hidden}
  .envelope .flap{position:absolute;left:0;right:0;top:0;height:40px;background:var(--navy)}
  .envelope .wordmark{position:absolute;left:22px;top:72px;font-size:18px}
  .envelope .tagline{position:absolute;left:22px;top:96px;font-size:5.5px;font-weight:700;letter-spacing:.1em;color:var(--ink)}
  .envelope .addr{position:absolute;left:22px;top:106px;font-size:5.5px;font-weight:700;color:var(--orange)}
  .envelope .bottom-bar{position:absolute;left:0;right:0;bottom:0;height:4px;background:linear-gradient(90deg,var(--navy) 0 36%,var(--orange) 36% 64%,var(--navy) 64%)}

  /* Notebook */
  .notebook{left:900px;top:482px;width:236px;height:366px;background:linear-gradient(180deg,var(--navy-light),var(--navy) 60%,var(--navy-deep));border-radius:0 12px 12px 0;border-left:6px solid #3a62b8;overflow:hidden}
  .notebook .wordmark{position:absolute;left:20px;top:112px;font-size:15px}
  .notebook .tagline{position:absolute;left:20px;top:134px;font-size:6.5px;font-weight:700;letter-spacing:.12em;color:var(--muted);white-space:nowrap}
  .notebook .band{position:absolute;right:22px;top:0;bottom:0;width:10px;background:#3f4448}
  .notebook .foot{position:absolute;left:0;right:0;bottom:0;height:28px;background:var(--orange);color:#fff;font-size:9px;font-weight:700;display:flex;align-items:center;padding-left:36px}
</style>
</head>
<body>

<!-- Letterhead -->
<section class="item letterhead" aria-label="Letterhead">
  <div class="head-rule"></div>
  <div class="wordmark on-light"><span class="dot"></span>Kestrel Cargo</div>
  <p class="footer-info">12 Harbor Rd, Easton, NJ 00000, United States &nbsp;|&nbsp; +1 000 000 0000 &nbsp;|&nbsp; contact@kestrelcargo.com</p>
  <div class="footer-bar"></div>
  <div class="site">www.kestrelcargo.com</div>
</section>

<!-- Presentation folder -->
<section class="item folder" aria-label="Presentation folder">
  <div class="panel back">
    <svg class="wave" viewBox="0 0 360 430" preserveAspectRatio="none">
      <defs>
        <linearGradient id="backScene" x1="0" y1="0" x2="1" y2="1">
          <stop offset="0" stop-color="#2f7fb5"/><stop offset="1" stop-color="#0d4a72"/>
        </linearGradient>
      </defs>
      <path d="M0 0 H300 C300 120 40 150 0 300 Z" fill="url(#backScene)" role="img" aria-label="Photograph of cargo trucks and a global network"/>
      <path d="M300 0 C300 120 40 150 0 300" fill="none" stroke="#c9d8e4" stroke-width="3"/>
    </svg>
    <div class="wordmark on-dark"><span class="dot"></span>Kestrel Cargo</div>
    <div class="contacts">
      <div class="contact">
        <span class="badge"><svg width="11" height="11" viewBox="0 0 24 24" fill="#fff"><path d="M6.6 10.8a15 15 0 0 0 6.6 6.6l2.2-2.2c.3-.3.7-.4 1-.2 1.1.4 2.3.6 3.6.6.6 0 1 .4 1 1V20c0 .6-.4 1-1 1A17 17 0 0 1 3 4c0-.6.4-1 1-1h3.5c.6 0 1 .4 1 1 0 1.3.2 2.5.6 3.6.1.3 0 .7-.2 1z"/></svg></span>
        +1 000 000 0000<br>kestrelcargo.com
      </div>
      <div class="contact">
        <span class="badge"><svg width="11" height="11" viewBox="0 0 24 24" fill="#fff"><path d="M3 5h18v14H3z M3 5l9 7 9-7" stroke="#f26a3a" stroke-width="1.5"/></svg></span>
        info@kestrelcargo.com
      </div>
      <div class="contact">
        <span class="badge"><svg width="11" height="11" viewBox="0 0 24 24" fill="#fff"><path d="M12 3 2 12h3v8h5v-5h4v5h5v-8h3z"/></svg></span>
        Example Address
      </div>
    </div>
  </div>
  <div class="panel front">
    <svg class="wave" viewBox="0 0 360 430" preserveAspectRatio="none">
      <defs>
        <linearGradient id="frontScene" x1="0" y1="0" x2="1" y2="1">
          <stop offset="0" stop-color="#eaf3fb"/><stop offset="1" stop-color="#7fb2dc"/>
        </linearGradient>
      </defs>
      <path d="M360 150 C360 260 60 260 0 430 H360 Z" fill="url(#frontScene)" role="img" aria-label="Illustration of a city skyline with a truck, cargo ship and plane"/>
      <path d="M360 150 C360 260 60 260 0 430" fill="none" stroke="#c9d8e4" stroke-width="3"/>
    </svg>
    <div class="wordmark on-dark"><span class="dot"></span>Kestrel Cargo</div>
    <p class="tagline">Kestrel Cargo Company</p>
  </div>
</section>

<!-- Business card, front -->
<section class="item card card-front" aria-label="Business card front">
  <div class="wordmark on-dark"><span class="dot"></span>Kestrel Cargo</div>
  <p class="tagline">KESTREL CARGO COMPANY</p>
  <p class="site">kestrelcargo.com</p>
</section>

<!-- Business card, back -->
<section class="item card card-back" aria-label="Business card back">
  <div class="wordmark compact on-dark"><span class="dot"></span>Kestrel Cargo</div>
  <div class="divider"></div>
  <div class="details">
    <span class="name">Example Name</span>
    <span class="role">Designation</span>
    <span class="line-icon"><svg width="7" height="7" viewBox="0 0 24 24" fill="#f26a3a"><path d="M12 2a7 7 0 0 0-7 7c0 5 7 13 7 13s7-8 7-13a7 7 0 0 0-7-7z"/></svg>Example Address here</span>
    <span class="line-icon"><svg width="7" height="7" viewBox="0 0 24 24" fill="#f26a3a"><circle cx="12" cy="12" r="9"/></svg>000-000-0000</span>
    <span class="line-icon"><svg width="7" height="7" viewBox="0 0 24 24" fill="#f26a3a"><rect x="3" y="6" width="18" height="12"/></svg>hello@kestrelcargo.com</span>
  </div>
  <div class="stripe"></div>
</section>

<!-- Envelope -->
<section class="item envelope" aria-label="Envelope">
  <div class="flap"></div>
  <div class="wordmark on-light"><span class="dot"></span>Kestrel Cargo</div>
  <p class="tagline">KESTREL CARGO COMPANY</p>
  <p class="addr">Example Address here</p>
  <div class="bottom-bar"></div>
</section>

<!-- Notebook cover -->
<section class="item notebook" aria-label="Notebook cover">
  <div class="wordmark on-dark"><span class="dot"></span>Kestrel Cargo</div>
  <p class="tagline">KESTREL CARGO COMPANY</p>
  <div class="foot">www.kestrelcargo.com</div>
  <div class="band"></div>
</section>

</body>
</html>
```